Executive Business Card for Healthcare Company [Need Today]

I need a business card design for a healthcare company. The only branding the company has thus far is a logo. The cards will be utilized by company executives. The design I envision will be vibrant and appealing but with a corporate feel. They shouldn't be too casual or playful. I would like to complete this project TODAY if possible.

Target Market(s)

Healthcare vendors, other executives in healthcare and pharmaceuticals

Industry/Entity Type

Pharmaceutical

Contact Information for Business Card

See attachment

Font styles to use
Serif
Sans Serif

Colors

Designer to choose colors to be used in the design.

```html
<!DOCTYPE html>
<html lang="en">
<head>
<meta charset="utf-8">
<title>Lumora Therapeutics – Business Card</title>
<link rel="stylesheet" href="https://fonts.googleapis.com/css2?family=Open+Sans:wght@300;400&family=Roboto+Condensed:wght@500&display=swap">
<style>
  :root {
    --canvas-bg: #9c9c9c;
    --teal: #36bfc6;
    --teal-line: #3cc4cc;
    --green: #45a878;
    --name-green: #3a9a5c;
    --paper: #f3f3f3;
    --ink: #333333;
    --white: #ffffff;
  }
  * { margin: 0; padding: 0; box-sizing: border-box; }
  html, body {
    width: 1200px; height: 1000px; overflow: hidden;
    background: var(--canvas-bg);
    font-family: "Open Sans", sans-serif;
  }
  .card {
    position: absolute;
    left: 250px;
    width: 700px;
    height: 418px;
    overflow: hidden;
  }
  /* Front side */
  .card-front { top: 62px; background: var(--teal); }
  .card-front .pattern-area {
    position: absolute; inset: 0;
    background: var(--teal);
  }
  .brand {
    position: absolute;
    display: flex;
    align-items: center;
    font-family: "Open Sans", sans-serif;
    font-weight: 300;
  }
  .brand-circle {
    border-radius: 50%;
    flex: none;
  }
  .brand-name { line-height: 1; }
  .brand-name .word-main { display: block; }
  .brand-name .word-sub { display: block; }

  .card-front .brand { left: 113px; top: 176px; color: var(--white); }
  .card-front .brand-circle {
    width: 106px; height: 106px;
    border: 2px solid var(--white);
    margin-right: 34px;
  }
  .card-front .word-main { font-size: 56px; letter-spacing: 1px; }
  .card-front .word-sub { font-size: 30px; margin-top: 4px; padding-left: 100px; }

  /* Back side */
  .card-back { top: 532px; background: var(--paper); }
  .card-back .brand { left: 345px; top: 33px; color: var(--teal); }
  .card-back .brand-circle {
    width: 96px; height: 96px;
    border: 2px solid var(--teal);
    margin-right: 22px;
  }
  .card-back .word-main { font-size: 42px; letter-spacing: 1px; }
  .card-back .word-sub { font-size: 22px; margin-top: 2px; padding-left: 72px; color: var(--teal); }

  .person { position: absolute; left: 37px; top: 247px; }
  .person-name {
    font-family: "Roboto Condensed", sans-serif;
    font-weight: 500;
    font-size: 21px;
    color: var(--name-green);
    letter-spacing: 0.5px;
  }
  .person-title { font-size: 16px; color: var(--ink); margin-top: 1px; }

  .contact-list {
    position: absolute; left: 37px; top: 313px;
    list-style: none; font-size: 14.5px; color: var(--ink); line-height: 19.5px;
  }
  .contact-list li { display: flex; align-items: center; }
  .contact-list .icon { width: 12px; height: 12px; margin-right: 5px; flex: none; }
  .contact-list .no-icon { padding-left: 17px; }

  .company-address {
    position: absolute; left: 487px; top: 313px;
    font-style: normal; font-size: 14.5px; color: var(--ink); line-height: 19.5px;
  }
  .card-band { position: absolute; left: 0; bottom: 0; width: 700px; height: 40px; }
</style>
</head>
<body>

<section class="card card-front" aria-label="Card front">
  <div class="pattern-area" role="img" aria-label="Faint repeating brand pattern"></div>
  <div class="brand">
    <span class="brand-circle"></span>
    <span class="brand-name">
      <span class="word-main">lumora</span>
      <span class="word-sub">therapeutics</span>
    </span>
  </div>
</section>

<section class="card card-back" aria-label="Card back">
  <div class="brand">
    <span class="brand-circle"></span>
    <span class="brand-name">
      <span class="word-main">lumora</span>
      <span class="word-sub">therapeutics</span>
    </span>
  </div>

  <div class="person">
    <h1 class="person-name">DANIEL REYES</h1>
    <p class="person-title">Senior Director of Marketing</p>
  </div>

  <ul class="contact-list">
    <li>
      <svg class="icon" viewBox="0 0 12 12" aria-hidden="true">
        <circle cx="6" cy="6" r="6" fill="#45a878"/>
        <path d="M3.6 3.2l1.2-.4.7 1.6-.7.6c.3.8.9 1.4 1.7 1.7l.6-.7 1.6.7-.4 1.2c-2.6.2-4.9-2.1-4.7-4.7z" fill="#fff"/>
      </svg>555-014-2230 (Office)
    </li>
    <li class="no-icon">555-017-6684 (Cell)</li>
    <li>
      <svg class="icon" viewBox="0 0 12 12" aria-hidden="true">
        <rect x="0.5" y="1.5" width="11" height="9" rx="1.5" fill="#45a878"/>
        <path d="M2 3.5l4 3 4-3" stroke="#fff" stroke-width="1" fill="none"/>
      </svg>dreyes@lumorarx.com
    </li>
  </ul>

  <address class="company-address">
    Lumora Therapeutics, LLC<br>
    118 W Meadow Street<br>
    Fairview, GA 30000
  </address>

  <svg class="card-band" viewBox="0 0 700 40" preserveAspectRatio="none" aria-hidden="true">
    <path d="M0 22 H400 Q412 22 420 16 L422 14 H700 V40 H0 Z" fill="var(--green)"/>
    <path d="M0 22 H400 Q412 22 420 16 L426 12" stroke="var(--teal-line)" stroke-width="5" fill="none"/>
    <path d="M0 27 H700" stroke="var(--teal-line)" stroke-width="0" fill="none"/>
    <rect x="0" y="22" width="410" height="3" fill="#ffffff"/>
    <rect x="0" y="25" width="700" height="15" fill="var(--green)"/>
  </svg>
</section>

</body>
</html>
```